Business Cards Design for the electrical wholesaler: clean bold dynamic :)

We need a business card design that would follow our latest brand guidelines. As an electrical wholesaler we want to bring a fresh look and feel into the industry. The design should be clean bold and dynamic. It should come alive with the renewed energy of our green colour. Our grey colour should keep things balanced and complement the notion of maturity and responsibility. We employ Lato as a corporate font however are not bound by this font and we’re open to interpretation here.

Target Market(s)

Electrical contractors

Industry/Entity Type

Business

Contact Information for Business Card

Logo
Name & Surname: Halyna Dorosh
Job Title: Director of Marketing
Email: halya.dorosh@quillmail.example
Cell phone: XXX.XXX.XXXX
Address: 20517 - 87 Ave. Edmonton, AB, Canada. T6K 4N8
Business Phone: 780.555.0184
Website: www.brovix.example

Font styles to use
Other font styles liked:
• Lato

Requirements
Must have
• Logo & website
Nice to have
• Brand elements - some of them you may find in the attached Brand Guidelines (e.g. three lines on the background signifying "W")

```html
<!DOCTYPE html>
<html lang="en">
<head>
<meta charset="utf-8">
<title>Brovix Business Cards</title>
<link rel="stylesheet" href="https://fonts.googleapis.com/css2?family=Exo+2:wght@500&family=Roboto:wght@400;500&display=swap">
<style>
  :root {
    --backdrop: #bdbdbd;
    --charcoal: #45484c;
    --paper: #f3f3f1;
    --green: #7dbd2b;
    --text-dark: #3f4246;
    --text-light: #e9eaea;
  }
  * { box-sizing: border-box; margin: 0; padding: 0; }
  html, body {
    width: 1200px; height: 576px; overflow: hidden;
    background: var(--backdrop);
    font-family: "Roboto", sans-serif;
  }
  .canvas { position: relative; width: 1200px; height: 576px; }
  .card {
    position: absolute; top: 138px;
    width: 484px; height: 293px;
    border-radius: 14px; overflow: hidden;
  }
  .card--front { left: 82px; background: var(--charcoal); }
  .card--back { left: 602px; background: var(--paper); }

  .brand {
    position: absolute; display: flex; align-items: center; gap: 10px;
    font-family: "Roboto", sans-serif; font-weight: 500; line-height: 1;
  }
  .brand__dot { border-radius: 50%; background: var(--green); flex: none; }
  .card--front .brand { left: 110px; top: 124px; font-size: 44px; color: #ffffff; }
  .card--front .brand__dot { width: 30px; height: 30px; }
  .card--back .brand { left: 27px; top: 38px; font-size: 38px; color: var(--text-dark); }
  .card--back .brand__dot { width: 26px; height: 26px; }

  .band {
    position: absolute; left: 0; top: 112px; width: 100%; height: 134px;
    background: var(--charcoal);
  }
  .person { position: absolute; left: 27px; top: 22px; }
  .person__name {
    font-family: "Exo 2", sans-serif; font-weight: 500;
    font-size: 20px; color: var(--green); line-height: 1;
  }
  .person__title { margin-top: 7px; font-size: 12.5px; color: var(--text-light); line-height: 1.2; }

  .contacts {
    position: absolute; left: 27px; top: 76px;
    font-size: 12.5px; color: var(--text-light); line-height: 1.2;
    display: flex; flex-direction: column; gap: 4px;
  }
  .contacts__row { display: flex; align-items: center; gap: 12px; white-space: nowrap; }
  .contact { display: flex; align-items: center; gap: 7px; }
  .contact__icon { width: 13px; height: 13px; flex: none; }
  .contact__accent { color: var(--green); }

  .address {
    position: absolute; left: 27px; top: 262px;
    font-size: 12.5px; color: var(--text-dark); line-height: 1.2;
  }
</style>
</head>
<body>
<main class="canvas">
  <section class="card card--front" aria-label="Card front">
    <div class="brand"><span class="brand__dot"></span>brovix</div>
  </section>

  <section class="card card--back" aria-label="Card back">
    <div class="brand"><span class="brand__dot"></span>brovix</div>

    <div class="band">
      <div class="person">
        <p class="person__name">Halyna Dorosh</p>
        <p class="person__title">Director of Marketing</p>
      </div>

      <div class="contacts">
        <div class="contacts__row">
          <span class="contact">
            <svg class="contact__icon" viewBox="0 0 14 14" aria-hidden="true">
              <circle cx="7" cy="7" r="6.2" fill="none" stroke="#7dbd2b" stroke-width="1.2"/>
              <path d="M4.6 3.8l1.3 0 .6 1.6-.8.6a4.3 4.3 0 0 0 2.2 2.2l.6-.8 1.6.6 0 1.3c-3.2.3-5.8-2.3-5.5-5.5z" fill="#7dbd2b"/>
            </svg>
            +1 780-555-0184
          </span>
        </div>
        <div class="contacts__row">
          <span class="contact">
            <svg class="contact__icon" viewBox="0 0 14 14" aria-hidden="true">
              <circle cx="7" cy="7" r="6.2" fill="none" stroke="#7dbd2b" stroke-width="1.2"/>
              <rect x="3.8" y="4.8" width="6.4" height="4.4" fill="#7dbd2b"/>
              <path d="M3.8 4.8l3.2 2.4 3.2-2.4" fill="none" stroke="#45484c" stroke-width=".7"/>
            </svg>
            halya.dorosh@quillmail.example
          </span>
          <span class="contact">
            <svg class="contact__icon" viewBox="0 0 14 14" aria-hidden="true">
              <circle cx="7" cy="7" r="6.2" fill="none" stroke="#7dbd2b" stroke-width="1.2"/>
              <circle cx="7" cy="7" r="3.4" fill="#7dbd2b"/>
            </svg>
            <span>www.<span class="contact__accent">brovix</span>.example</span>
          </span>
        </div>
      </div>
    </div>

    <p class="address">20517 - 87 Ave. Edmonton, AB, Canada T6K 4N8</p>
  </section>
</main>
</body>
</html>
```